Buchcover-Design für Fragenbuch
Ganz herzlichen Dank. Die Zusammenarbeit war völlig reibungslos und entspannt. Änderungswünsche wurden professionell umgesetzt und die kreativen Vorschläge fand ich super. Ich bin total glücklich mit dem Ergebnis.
Zielgruppe
Autorin und Workshopleiterin. Zielgruppe: Frauen ab 30
Aufgabenstellung
Ich benötige ein komplettes Buchcover, sowie 12 farbige Innenseiten. Es geht um ein Fragenbuch zum Ausfüllen mit dem Titel:
„Umarme deine stille Seele
Das Arbeitsheft zum Eintragen für neue seelische Balance“
Das Format des Buches beträgt 17x22cm. Es ist in 12 Wochen unterteilt. Darum hätte ich gerne zwischen den einzelnen Wochen eine farbige Seite (1. Woche, 2. Woche etc.), die designmäßig mit dem Außencover korrespondiert.
Die Farben sollten eher zart oder gedeckt sein. Auf keinen Fall jedoch kitschig. Wichtig ist mir, dass keine bestimmte Person zu sehen ist. (Foto)
Das ist meine Website www.umarme-deine-stille-seele.de

```html
<!DOCTYPE html>
<html lang="de">
<head>
<meta charset="utf-8">
<title>Umarme deine stille Seele – Cover und Wochenseite</title>
<link rel="stylesheet" href="https://fonts.googleapis.com/css2?family=Sorts+Mill+Goudy&family=Open+Sans:wght@400&display=swap">
<style>
  :root {
    --canvas: #ffffff;
    --paper: #e6dbc8;
    --rule: #b0693a;
    --ink: #4a2418;
    --ink-deep: #3a1a12;
    --photo-flower: linear-gradient(160deg, #d8b48c 0%, #c59a6e 45%, #a88a72 75%, #cbbcaa 100%);
    --photo-room: linear-gradient(150deg, #cfc7bc 0%, #bfb3a4 40%, #a07a52 65%, #e0ddd6 100%);
  }
  * { box-sizing: border-box; margin: 0; padding: 0; }
  html, body { width: 1200px; height: 849px; overflow: hidden; background: var(--canvas); }
  .spread { position: relative; width: 1200px; height: 849px; }

  .page {
    position: absolute; top: 184px; width: 361px; height: 468px;
    background: var(--paper);
    box-shadow: 9px 9px 10px rgba(0,0,0,0.45);
    font-family: "Sorts Mill Goudy", Georgia, serif;
    color: var(--ink);
  }
  .page--cover { left: 233px; }
  .page--week { left: 663px; }

  .rule { position: absolute; background: var(--rule); }
  .rule--h { height: 1px; }
  .rule--v { width: 1px; }

  .photo {
    position: absolute; border-bottom-right-radius: 90px;
  }
  .photo--flower { left: 94px; top: 50px; width: 180px; height: 239px; background: var(--photo-flower); }
  .photo--room { left: 86px; top: 49px; width: 179px; height: 240px; background: var(--photo-room); }

  .cover-title {
    position: absolute; left: 0; width: 361px; top: 304px;
    text-align: center; font-size: 19.5px; text-transform: uppercase; letter-spacing: 0.2px;
  }
  .cover-subtitle {
    position: absolute; left: 0; width: 361px; top: 339px;
    text-align: center; font-size: 16px; font-variant: small-caps;
  }
  .cover-claim {
    position: absolute; left: 61px; width: 239px; top: 389px;
    text-align: center; font-family: "Open Sans", Arial, sans-serif;
    font-size: 7.5px; line-height: 11px; text-transform: uppercase;
  }
  .cover-footer {
    position: absolute; left: 61px; width: 239px; top: 427px;
    display: flex; justify-content: space-evenly; align-items: center;
    font-size: 7px;
  }
  .cover-footer .author { font-style: italic; font-size: 8px; }

  .week-number {
    position: absolute; left: 40px; top: 250px;
    font-size: 66px; line-height: 1; color: var(--ink-deep);
  }
  .week-label {
    position: absolute; left: 290px; top: 230px; width: 18px;
    text-align: center; font-size: 16px; line-height: 19.5px; color: var(--ink-deep);
  }
  .section-headline {
    position: absolute; left: 60px; width: 238px; top: 355px;
    text-align: center; font-size: 19px; text-transform: uppercase;
  }
  .section-title {
    position: absolute; left: 60px; width: 238px; top: 411px;
    text-align: center; font-size: 17px; font-variant: small-caps;
  }
</style>
</head>
<body>
<main class="spread">

  <section class="page page--cover" aria-label="Buchcover">
    <div class="rule rule--h" style="left:61px;top:23px;width:240px"></div>
    <div class="rule rule--v" style="left:61px;top:23px;height:281px"></div>
    <div class="rule rule--v" style="left:300px;top:23px;height:281px"></div>
    <div class="rule rule--v" style="left:61px;top:328px;height:117px"></div>
    <div class="rule rule--v" style="left:300px;top:328px;height:117px"></div>
    <div class="rule rule--h" style="left:61px;top:381px;width:240px"></div>
    <div class="rule rule--h" style="left:61px;top:420px;width:240px"></div>
    <div class="rule rule--h" style="left:61px;top:444px;width:240px"></div>

    <div class="photo photo--flower" role="img" aria-label="Nahaufnahme einer getrockneten Blüte in warmen Beigetönen"></div>

    <h1 class="cover-title">Umarme deine stille Seele</h1>
    <p class="cover-subtitle">Das Arbeitsheft</p>
    <p class="cover-claim">Zum Eintragen<br>für neue seelische Balance</p>
    <p class="cover-footer">
      <span>Coaching</span><span>Mentoring</span><span class="author">by Lena Morvik</span><span>2021</span>
    </p>
  </section>

  <section class="page page--week" aria-label="Wochenseite">
    <div class="rule rule--h" style="left:57px;top:23px;width:242px"></div>
    <div class="rule rule--v" style="left:57px;top:23px;height:190px"></div>
    <div class="rule rule--v" style="left:298px;top:23px;height:190px"></div>
    <div class="rule rule--v" style="left:60px;top:341px;height:104px"></div>
    <div class="rule rule--v" style="left:298px;top:341px;height:104px"></div>
    <div class="rule rule--h" style="left:60px;top:401px;width:239px"></div>
    <div class="rule rule--h" style="left:60px;top:444px;width:239px"></div>

    <div class="photo photo--room" role="img" aria-label="Helles Wohninterieur mit Spiegel, Konsole und Vase mit Pampasgras"></div>

    <span class="week-number">2</span>
    <p class="week-label">W<br>O<br>C<br>H<br>E</p>
    <h2 class="section-headline">Section Headline</h2>
    <p class="section-title">Title here</p>
  </section>

</main>
</body>
</html>
```